Veltrane Group Business Card Design

The CEO is looking for a new trendy look for his business card.
You can stay with current branding or come up with something new/creative. It can be 3D, including Medical Office buildings. You can use our logo in a variety of colors. Please include name, title, company name, company website, email address, cell number

Target Market(s)

Real Estate Development and Construction

Industry/Entity Type

Health care real estate

Contact Information for Business Card

Rohesh Kamdar, CEO M-604.781.2249 E-roheshkamdar@veltrane.com Address:4180 Lindqvist Ave, Tampa, FL 33482 www.veltrane.com

Font styles to use
Other font styles liked:
• Be creative

Requirements
Must have
• Creative, trendy look
Nice to have
• Please go to our website to get a feel- www. veltrane.com
Should not have
• small fonts

```html
<!DOCTYPE html>
<html lang="en">
<head>
<meta charset="utf-8">
<title>Veltrane Group Business Card</title>
<link href="https://fonts.googleapis.com/css2?family=Montserrat:wght@400;700&display=swap" rel="stylesheet">
<style>
  :root {
    --backdrop: #2a2a2a;
    --card-dark: #1e1e1e;
    --card-light: #ffffff;
    --ink-light: #ffffff;
    --ink-muted: #d6d6d6;
    --ink-dark: #111111;
  }
  * { margin: 0; padding: 0; box-sizing: border-box; }
  html, body {
    width: 1200px; height: 1015px; overflow: hidden;
    background: var(--backdrop);
    font-family: "Montserrat", Arial, sans-serif;
  }
  .stage { position: relative; width: 1200px; height: 1015px; }
  .card {
    position: absolute; left: 250px; width: 700px; height: 400px;
    background: var(--card-dark);
    box-shadow: 0 10px 30px rgba(0,0,0,.45);
    overflow: hidden;
  }
  .card--front { top: 70px; display: flex; align-items: center; justify-content: center; }
  .card--back { top: 545px; }

  .brand-name {
    font-weight: 700; white-space: nowrap; line-height: 1;
    color: var(--ink-light);
  }
  .card--front .brand-name { font-size: 56px; }

  .back__info {
    position: absolute; left: 60px; top: 60px; bottom: 50px; width: 420px;
    color: var(--ink-light);
    display: flex; flex-direction: column; justify-content: space-between;
  }
  .person__name { font-size: 24px; font-weight: 700; }
  .person__title { font-size: 14px; color: var(--ink-muted); margin-top: 4px; margin-left: 18px; }

  .contact { font-size: 15px; color: var(--ink-muted); }
  .contact__address { margin-bottom: 22px; line-height: 1.35; }
  .contact__list { list-style: none; }
  .contact__item { display: flex; align-items: center; gap: 12px; margin-top: 8px; }
  .contact__icon { width: 14px; height: 14px; flex: none; fill: var(--ink-light); }

  .back__brand {
    position: absolute; right: 0; top: 0; width: 200px; height: 100%;
    background: var(--card-light);
    display: flex; align-items: center; justify-content: center;
  }
  .back__brand .brand-name { color: var(--ink-dark); font-size: 18px; }
</style>
</head>
<body>
<main class="stage">
  <section class="card card--front" aria-label="Card front">
    <p class="brand-name">Veltrane Group</p>
  </section>

  <section class="card card--back" aria-label="Card back">
    <div class="back__info">
      <div class="person">
        <p class="person__name">Rohesh Kamdar</p>
        <p class="person__title">CEO</p>
      </div>
      <div class="contact">
        <p class="contact__address">4180 Lindqvist Ave,<br>Tampa, FL 33482</p>
        <ul class="contact__list">
          <li class="contact__item">
            <svg class="contact__icon" viewBox="0 0 16 16" aria-hidden="true"><path d="M3.5 1l2.5 3-1.5 2a9 9 0 0 0 5 5l2-1.5 3 2.5-1.5 2.5C6.5 15 1 9.5 1 2.5z"/></svg>
            <span>604.781.2249</span>
          </li>
          <li class="contact__item">
            <svg class="contact__icon" viewBox="0 0 16 16" aria-hidden="true"><path d="M1 3h14v10H1z M1 3l7 6 7-6" fill="none" stroke="#fff" stroke-width="1.6"/></svg>
            <span>roheshkamdar@veltrane.com</span>
          </li>
          <li class="contact__item">
            <svg class="contact__icon" viewBox="0 0 16 16" aria-hidden="true"><circle cx="8" cy="8" r="6.5" fill="none" stroke="#fff" stroke-width="1.5"/><path d="M1.5 8h13M8 1.5c-3 3.5-3 9.5 0 13M8 1.5c3 3.5 3 9.5 0 13" fill="none" stroke="#fff" stroke-width="1.2"/></svg>
            <span>www.veltrane.com</span>
          </li>
        </ul>
      </div>
    </div>
    <div class="back__brand">
      <p class="brand-name">Veltrane Group</p>
    </div>
  </section>
</main>
</body>
</html>
```